Strategic Objective - Internal

Take text supplied in a word document and make a stylish, professional document using elements of our brand .This is an internal document for presentation to our small team . Have attached an example document - please do not copy this - this is just to give you the concept. I would like to be able to edit the text in the document you supply back to me also (In word or photoshop)

Our website is www.brolgatrade.com.au

Have attached out logo
Thank you

Target Market(s)

Our staff

Industry/Entity Type

Mining, Earthmoving

Requirements
Must have
• Professional, stylish presentation
Nice to have
• Our market includes Australia, Papua New Guinea and teh South Pacific - any graphic that supports this. We are an importer and exporter - any graphics that support this.

```html
<!DOCTYPE html>
<html lang="en">
<head>
<meta charset="utf-8">
<title>Kestrel Supply – Strategic Objectives 2024-2025</title>
<link href="https://fonts.googleapis.com/css2?family=Roboto:wght@300;400;500;700&display=swap" rel="stylesheet">
<style>
:root{
  --navy:#373d85;
  --navy-deep:#2c3274;
  --green:#7cbd43;
  --green-soft:#8fc95c;
  --cream:#fdf1e0;
  --mint:#e9f3df;
  --paper:#ffffff;
  --paper-grey:#f1f1f1;
  --backdrop:#e1e1e1;
  --ink:#4a4a4a;
  --blue:#2c9fd9;
  --gold:#f0b323;
}
*{box-sizing:border-box;margin:0;padding:0}
html,body{width:1200px;height:1063px;overflow:hidden}
body{background:var(--backdrop);font-family:"Roboto",Arial,sans-serif;color:var(--ink);position:relative}
.page{position:absolute;width:344px;height:457px;background:var(--paper);overflow:hidden;box-shadow:0 3px 10px rgba(0,0,0,.25)}
.abs{position:absolute}
.logo{position:absolute;top:18px;right:26px;display:flex;align-items:center;gap:4px;font:700 10px/1 "Roboto",Arial,sans-serif;color:var(--navy);letter-spacing:.2px}
.logo::before{content:"";width:9px;height:9px;border-radius:50%;background:var(--green)}
.on-dark .logo{color:#fff}
h2{font:700 13px/1.1 "Roboto",Arial,sans-serif;color:var(--navy)}
.light{color:#fff}
p,li{font-size:6px;line-height:1.45;font-weight:300}
ul{list-style:none}
ul.dots li{padding-left:7px;position:relative;margin-bottom:2px}
ul.dots li::before{content:"•";position:absolute;left:0}
.ph{position:absolute}

/* page 1 */
.p1{left:54px;top:63px}
.stat{position:absolute;width:63px;height:49px;background:var(--green);color:#fff;text-align:center;padding-top:9px}
.stat b{display:block;font:500 13px/1 "Roboto",Arial,sans-serif}
.stat span{display:block;font-size:6px;line-height:1.2;margin-top:3px;font-weight:300}

/* page 2 */
.p2{left:427px;top:63px;background:var(--cream)}
.p2 .top{position:absolute;left:0;top:0;width:344px;height:247px;background:var(--navy)}
.value{position:absolute;width:170px}
.value h3{font:500 8px/1 "Roboto",Arial,sans-serif;color:var(--green);margin-bottom:2px}
.value p{color:#fff;font-size:5px;line-height:1.35}

/* page 3 */
.p3{left:801px;top:63px;background:var(--paper-grey)}
.quote{position:absolute;left:66px;top:165px;width:235px;height:54px;background:#fff;padding:6px 8px}
.quote p{font-size:5px;line-height:1.4}
.band{position:absolute;left:0;top:253px;width:344px;height:204px;background:var(--green)}
.mind{position:absolute;left:22px;top:312px;width:322px;height:145px;background:var(--navy)}
.mind li{color:#fff;font-size:5px;line-height:1.35;margin-bottom:2px}

/* page 4 */
.p4{left:54px;top:542px;background:var(--navy)}
.p4 .side{position:absolute;left:0;top:0;width:164px;height:457px;background:var(--mint)}
.p4 .side h2{color:var(--navy)}
.p4 .side p{font-size:5.6px;margin-bottom:4px;color:var(--ink)}
.p4 .right h2{color:#fff}
.p4 .right li,.p4 .right p{color:#fff;font-size:5.6px}
.p4 .right li{margin-bottom:4px}

/* page 5 */
.p5{left:427px;top:542px;background:var(--navy)}
.tile{position:absolute;width:150px;color:#fff}
.tile h4{font:700 7.5px/1.2 "Roboto",Arial,sans-serif;margin-bottom:1px}
.tile p{font-size:5.6px;line-height:1.4}
.ring{position:absolute;width:34px;height:34px;border:1.5px solid #fff;border-radius:50%;background:var(--navy-deep)}
.ops{position:absolute;left:0;top:319px;width:165px;height:138px;background:var(--green);padding:16px 0 0 33px;color:#fff}
.ops p{font-size:5.8px;line-height:1.4;width:120px}
</style>
</head>
<body>

<!-- Page 1 : Tangibles & Brand Promise -->
<section class="page p1">
  <div class="ph" style="left:0;top:78px;width:344px;height:185px;background:linear-gradient(180deg,#ffffff 0%,#d9d9d6 18%,#9a9b95 60%,#6f706b 100%)" role="img" aria-label="Photograph of a large mining haul truck in a quarry"></div>
  <div class="logo">Kestrel Supply</div>
  <h2 class="abs" style="left:33px;top:42px">Tangibles</h2>
  <p class="abs" style="left:33px;top:60px;font-size:6.4px">In the 2024-2025 Financial year we will have</p>
  <p class="abs" style="left:33px;top:72px;font-size:8px">Annual turnover of <b style="font-weight:700;color:var(--navy);font-size:10px">18M</b></p>
  <div class="stat" style="left:33px;top:104px"><b>21%</b><span>Gross profit</span></div>
  <div class="stat" style="left:106px;top:104px"><b>200</b><span>Average Quotes<br>per week</span></div>
  <div class="stat" style="left:33px;top:163px"><b>52%</b><span>Conversion<br>rate</span></div>
  <div class="stat" style="left:106px;top:163px"><b>10%</b><span>Annual<br>growth rate</span></div>
  <h2 class="abs" style="left:33px;top:283px">Our Brand Promise</h2>
  <div class="abs" style="left:33px;top:302px;width:160px">
    <p style="margin-bottom:6px">In every interaction with our business our customers know that they are working with the best – they will not find better service or overall value anywhere else – and this gets reinforced by every interaction they have with us. As well as the physical products they are buying peace of mind.</p>
    <p>We define being the best in terms of Knowledge, Responsiveness, Accuracy, Competitive pricing, Consistency and Understanding</p>
  </div>
  <div class="ph" style="left:203px;top:330px;width:127px;height:88px;border-radius:40px 10px 10px 40px;background:linear-gradient(135deg,#eef0f5,#e3e6ee)" role="img" aria-label="Illustration of two business people shaking hands"></div>
</section>

<!-- Page 2 : Core Values & Culture -->
<section class="page p2">
  <div class="top on-dark"><div class="logo">Kestrel Supply</div></div>
  <svg class="abs" style="left:0;top:0" width="344" height="247" viewBox="0 0 344 247" aria-hidden="true">
    <path d="M87 82 Q140 95 138 112 M138 112 L138 168 M138 168 Q140 190 87 200" fill="none" stroke="var(--green)" stroke-width="5"/>
    <circle cx="87" cy="82" r="23" fill="#fff" stroke="#2b2f6b" stroke-width="3"/>
    <circle cx="138" cy="112" r="21" fill="#fff" stroke="var(--green)" stroke-width="3"/>
    <circle cx="138" cy="168" r="21" fill="#fff" stroke="var(--gold)" stroke-width="3"/>
    <circle cx="87" cy="200" r="23" fill="#fff" stroke="var(--blue)" stroke-width="3"/>
    <g fill="none" stroke="var(--navy)" stroke-width="1.4">
      <path d="M77 82 l7 -6 l7 6 l-7 6 z"/>
      <circle cx="138" cy="112" r="7"/><path d="M133 112 l3 3 l6 -6"/>
      <path d="M130 176 l5 -6 l4 3 l7 -9"/><path d="M142 164 h4 v4"/>
      <rect x="79" y="194" width="16" height="11" rx="2"/>
    </g>
  </svg>
  <div class="abs" style="left:30px;top:135px;font:700 14px/1.25 'Roboto',Arial,sans-serif;color:#fff">OUR CORE<br>&nbsp;&nbsp;VALUES</div>
  <div class="value" style="left:116px;top:45px;width:210px"><h3>Commitment to Excellence</h3><p>We turn up every day ready to be the best person we can be and deliver the best possible outcome and experience for our customer. Set a high bar and always seek to improve.</p></div>
  <div class="value" style="left:169px;top:98px;width:120px"><h3>Accuracy</h3><p>How we do the little things is how we do everything. Detail matters. We never assume…we make certain</p></div>
  <div class="value" style="left:169px;top:155px;width:110px"><h3>Growth</h3><p>Our knowledge, Experience, and Skills. Personal &amp; professional. Be curious and interested.</p></div>
  <div class="value" style="left:117px;top:206px;width:200px"><h3>Respect</h3><p>Listen first and understand. Everyone is valued.</p></div>
  <h2 class="abs" style="left:29px;top:268px;font-size:12px">Our Culture</h2>
  <p class="abs" style="left:29px;top:283px;width:290px;font-size:5.6px">We pride ourselves on a collaborative and harmonious work environment where we support each other respectfully. Every team member feels seen, heard, and understood. Team members must love the company before the clients can love the company. Our team members truly want to work here…not because of the paycheck but because they feel valued, enjoy what they do and are making a difference to our clients’ businesses and lives.</p>
  <p class="abs" style="left:29px;top:342px;width:176px;font-size:5.6px">Our Team members are confident enough to have hard conversations while always assuming the best intentions of their fellow team member. Team members hold each other accountable for what they are supposed to be doing because it is the right thing to do. Team members can honestly tell their family and friends that they love working for our company. Team members give more effort than expected because they want to, not because they must, or for a reward. All team members feel seen, heard, and understood</p>
  <div class="ph" style="left:208px;top:345px;width:136px;height:112px;border-radius:60px 0 0 30px;background:linear-gradient(160deg,#f2d9b8,#c9875a)" role="img" aria-label="Illustration of a team of construction workers collaborating"></div>
</section>

<!-- Page 3 : Commitment & A Team Member -->
<section class="page p3">
  <div class="logo">Kestrel Supply</div>
  <h2 class="abs" style="left:33px;top:42px;font-size:12px">At Kestrel Supply we are committed to…</h2>
  <ul class="dots abs" style="left:33px;top:61px;width:285px">
    <li>Compensating team members well.</li>
    <li>Making the highest priority our team members’: health, family, and growth. These three all come before work.</li>
    <li>Providing coaching and other forms of self-improvement.</li>
    <li>Having a friendly and welcoming environment.</li>
    <li>Having clarity around roles and responsibilities including regular mentoring</li>
    <li>Hiring and retaining the right team members that align with our values</li>
  </ul>
  <p class="abs" style="left:33px;top:152px;font-size:7px;font-weight:400;color:var(--navy)">Our goal is for team members to say:</p>
  <div class="abs" style="left:34px;top:180px;font:700 26px/1 'Roboto',Arial,sans-serif;color:var(--navy)">“</div>
  <div class="abs" style="left:59px;top:185px;width:2px;height:24px;background:var(--navy)"></div>
  <div class="quote"><p>I love working here” I enjoy doing working with our clients and suppliers and I know we are making a difference. I enjoy doing meaningful work. I am paid well for the work I am doing. I enjoy working with my colleagues and talking to them about what is happening in their personal and professional life. We have a great work environment. We work hard and have fun together.</p></div>
  <p class="abs" style="right:43px;top:228px;text-align:right;font-size:7px;font-weight:400;color:var(--navy)">Everyone who works here contributes to<br>creating the culture we want.</p>
  <div class="band"></div>
  <h2 class="abs light" style="left:36px;top:268px;font-size:12px">“A” Team Member</h2>
  <p class="abs light" style="left:33px;top:287px;font-size:7px">We have “A” team members in every seat…</p>
  <div class="mind">
    <p style="position:absolute;left:0;width:322px;top:8px;text-align:center;color:#fff;font:500 8px/1 'Roboto',Arial,sans-serif">Mindset</p>
    <ul class="dots" style="position:absolute;left:11px;top:44px;width:160px">
      <li>They have a “can do” attitude and are always ready to go the extra mile for our clients</li>
      <li>They are always friendly &amp; respectful to everyone else in the team, our customers &amp; our suppliers. They turn up each day eager to have a positive contribution to the work environment</li>
      <li>They speak up when something could be improved.</li>
      <li>They do what they say they are going to do</li>
      <li>They will do something they don’t like doing because that is what the company needs</li>
    </ul>
    <ul class="dots" style="position:absolute;left:177px;top:44px;width:138px">
      <li>“A” team members seek continuous improvement</li>
      <li>“A” team members self-reflect and evaluate themselves.</li>
      <li>They live the company’s core values at work</li>
      <li>They always strive to provide the best possible customer experience – Empathy, Knowledge, Responsiveness (speed), Accuracy, Competitive pricing, Consistency</li>
    </ul>
  </div>
  <div class="ph" style="left:20px;top:300px;width:42px;height:48px;border-radius:50% 50% 6px 6px;background:linear-gradient(180deg,#f3f3f3,#c9cbd6)" role="img" aria-label="Illustration of a smiling team member"></div>
</section>

<!-- Page 4 : Relationships, Markets & Client Experience -->
<section class="page p4 on-dark">
  <div class="side">
    <h2 class="abs" style="left:33px;top:54px;font-size:12px">Great Relationships</h2>
    <div class="abs" style="left:33px;top:72px;width:128px">
      <p>We are a business built on great relationships….. with each other, with our customers and with our suppliers.</p>
      <p>Our customer relationships are built on a foundation of consistently delivering outstanding service – they come to first because they trust us.</p>
      <p>Our suppliers help us because we value them and treat them fairly with respect and we always pay on time</p>
      <p>We pay attention to and nurture these relationships – they are what drive our business</p>
    </div>
    <h2 class="abs" style="left:33px;top:222px;font-size:12px">Markets Served</h2>
    <div class="abs" style="left:33px;top:239px;width:128px">
      <p style="margin-bottom:1px">Our primary market is</p>
      <p style="font-weight:700;font-size:7.5px;color:var(--navy);margin-bottom:1px">Papua New Guinea</p>
      <p>where approximately 90% of our revenue will come from. We will work with every mine in PNG (There are currently 8 operating and one due for construction. We deal with 6 of them now)</p>
      <p>The balance of our revenue will come from <b style="font-weight:700">Australia, Indonesia</b> and <b style="font-weight:700">New Caledonia</b></p>
      <p>We will continually seek and assess potential import &amp; distribution opportunities that further enhance our offering to clients, drive GP growth and create a competitive advantage.</p>
    </div>
    <div class="ph" style="left:133px;top:235px;width:19px;height:14px;background:linear-gradient(135deg,#111 50%,#c8102e 50%)" role="img" aria-label="National flag of Papua New Guinea"></div>
    <div class="ph" style="left:0;top:380px;width:133px;height:77px;border-radius:0 60% 0 0;background:radial-gradient(ellipse at 30% 60%,#3f7f3a,#9cc98b 70%,rgba(233,243,223,0) 100%)" role="img" aria-label="Map of Papua New Guinea and the South Pacific islands"></div>
  </div>
  <div class="logo">Kestrel Supply</div>
  <div class="ph" style="left:164px;top:330px;width:180px;height:127px;background:linear-gradient(180deg,rgba(55,61,133,1) 0%,#7d86a8 35%,#b59a82 70%,#5f7a91 100%)" role="img" aria-label="Photograph of a harbour city skyline at dusk"></div>
  <div class="right">
    <h2 class="abs" style="left:173px;top:54px;font-size:12px">Client Experience</h2>
    <p class="abs" style="left:173px;top:76px;width:160px">Our client experience is our competitive advantage. We cannot totally control our suppliers service level – but we can control everything that we do ourselves.</p>
    <ul class="dots abs" style="left:173px;top:114px;width:160px">
      <li><b style="font-weight:700">Responsiveness</b> – speed of communication, speed of quote,</li>
      <li><b style="font-weight:700">Empathy</b> – how we communicate with customers and suppliers, tone, Our ability put ourselves in our clients shoes and understand their needs</li>
      <li><b style="font-weight:700">Accuracy</b> – attention to detail, make certain, clarify, lead times</li>
      <li>Product Knowledge – what we know + how we learn, share &amp; store sourcing and product knowledge to provide a faster and better outcome for our customers</li>
      <li><b style="font-weight:700">Competitive pricing</b> – how well we source and negotiate discounts</li>
      <li><b style="font-weight:700">Consistency</b> – when our clients know they will get a great experience every time and trust us accordingly</li>
    </ul>
    <p class="abs" style="left:173px;top:308px;width:160px">We will have unsurpassed expertise in locating and supplying machine components &amp; parts from mining and earthmoving companies as well as extensive wholesale supplier relationships and supplier knowledge in Australia and overseas.</p>
  </div>
</section>

<!-- Page 5 : Team & Operations -->
<section class="page p5 on-dark">
  <div class="logo">Kestrel Supply</div>
  <div class="abs" style="left:0;top:39px;width:220px;height:66px;border-radius:0 33px 33px 0;background:var(--navy-deep)"></div>
  <div class="abs" style="left:33px;top:58px;font:700 17px/1.3 'Roboto',Arial,sans-serif;color:#fff">Team<br>2024-2025</div>
  <div class="ph" style="left:137px;top:24px;width:83px;height:81px;border-radius:40px 40px 0 0;background:linear-gradient(180deg,#f0c89b,#7cbd43)" role="img" aria-label="Illustration of a diverse group of team members"></div>
  <div class="ring" style="left:32px;top:126px"></div>
  <div class="ring" style="left:181px;top:126px"></div>
  <div class="ring" style="left:32px;top:229px"></div>
  <div class="ring" style="left:181px;top:207px"></div>
  <div class="tile" style="left:33px;top:165px;width:120px"><h4>13 staffs + CEO</h4><p>CEO role will be more involved with networking, strategic direction and less on-site</p><p style="margin-top:3px">Ops Manager responsible for all day-to-day business activities</p></div>
  <div class="tile" style="left:181px;top:165px;width:120px"><h4>3 Managers</h4><p>Customer Service, Finance, Warehouse</p></div>
  <div class="tile" style="left:181px;top:246px;width:120px"><p>Each role will have a Position Agreement, KPIs and commercial confidentiality agreement</p></div>
  <div class="tile" style="left:33px;top:267px;width:125px"><h4>Mentoring program</h4><p>for staff for professional growth (product training; negotiating; Excel) and personal growth</p></div>
  <div class="ops">
    <h2 style="color:#fff;font-size:12px;margin-bottom:6px">Operations</h2>
    <p>Modern Office with great work environment</p>
    <p style="font-weight:700;margin:4px 0 6px">300sqm <span style="font-weight:300">warehouse</span></p>
    <p>Best Practice systems and processes for all components of the customer journey and warehousing operations with a fully trained and committed team</p>
  </div>
  <div class="ph" style="left:165px;top:319px;width:179px;height:138px;background:linear-gradient(120deg,#8a6f55 0%,#c9a27a 40%,#d8d24a 75%,#3d6fa8 100%)" role="img" aria-label="Photograph of two warehouse workers in hard hats and hi-vis vests checking stock"></div>
</section>

</body>
</html>
```